Upgrade website from just a link tree to a full adult content site with payment gateway.

I would like to upgrade my website VelvetKestrel.com and turn it into a pay site with a payment gateway to my content. I would like to use Wordpress. The designer needs to produce a front page with membership sign up link, payment gateway which would then provide access to the content page. We would need to be able to then go in and edit (if necessary) and load all of the content. We would like this to be as easy as possible and already have paid for a Wordpress license. We could simply allow access to our hostnimbo/Wordpress account so you can build it once all the details are confirmed. Needs to be simple to upload and have a format all set to go where we would just log in and do it. May need directions or a tutorial to get us started on the path. We are open to suggestions and ideas. We will be providing adult content. Four pages I believe. Front page , gateway video content page and picture content page. The video and picture content goes really just need to be a layout and then we can drop the videos and images in there. You can ask any other relevant questions and we can update the brief. Sorry we are fairly new to this so this is why we are looking to professionals to lead the way. Please look at current webpage for an idea of how we like the current format. It can be replicated or it can be changed. We will market and funnel our online and SoCial accounts to this page on hopes people sign up and pay membership for access to the content past the first page. Check VelvetKestrel.com for an idea of how we want to move forward. Someone goes to page. We would like to see: They can click on member log in if they have already signed up or click join and go to the payment gateway page where they can choose their membership. Once they are paid they produce their log in and lassoed. Sign in and have access to the content pages. One page can be for photos and one page can be for videos. Would consider a live stream if possible but not mandatory. Basically we want to provide content people can view for a fee. A water mark would also be nice to protect our images and video. Also if there is a way to not allow the content to be downloaded. But a water mark would protect that.

Target Market(s)

Adult entertainment

Industry/Entity Type

Adult entertainment

Coding

Coded - Design and coding required

Number of Pages Required

4 page

Font styles to use
Decorative
Script

Colors
E54698
E96AAD
F1A4CE
F9D9EA
FCEFF6
A7469A
B969AE
D3A5CF
EDDBEB
F8F0F9

Requirements
Must have
• Front page. Gateway Payment/membership sign up. Video content page set up and image content page set up. Water mark we can put on content.
Nice to have
• Live video feed capabilities. Watermark.
Should not have
• Free access to the content.

```html
<!DOCTYPE html>
<html lang="en">
<head>
<meta charset="utf-8">
<title>VelvetKestrel – Thank You</title>
<link href="https://fonts.googleapis.com/css2?family=Montserrat:wght@400;500;600;700&display=swap" rel="stylesheet">
<style>
  :root {
    --pink: #eba5cd;
    --pink-strong: #e896c2;
    --white: #ffffff;
    --ink: #000000;
    --hero-dark: #1a1a1a;
    --hero-mid: #2c2c2c;
    --rule: #5a5a5a;
  }
  * { box-sizing: border-box; margin: 0; padding: 0; }
  html, body {
    width: 1200px; height: 676px; overflow: hidden;
    background: var(--ink);
    font-family: "Montserrat", Arial, sans-serif;
  }
  .page { position: relative; width: 1200px; height: 676px; }
  .hero {
    position: absolute; left: 0; top: 0; width: 1200px; height: 577px;
    border-bottom: 1px solid var(--rule);
  }
  .hero-photo {
    position: absolute; inset: 0;
    background:
      radial-gradient(ellipse 420px 260px at 560px 300px, #3a3a3a 0%, transparent 70%),
      radial-gradient(ellipse 500px 200px at 1050px 150px, #353535 0%, transparent 70%),
      linear-gradient(160deg, var(--hero-mid) 0%, var(--hero-dark) 55%, #222 100%);
  }
  .contact {
    position: absolute; right: 99px; top: 24px;
    display: flex; align-items: center; gap: 11px;
    color: var(--white); font-size: 14px; font-weight: 500;
  }
  .brand {
    position: absolute; left: 58px; top: 62px;
    color: var(--white); font-size: 30px; font-weight: 500; letter-spacing: 0.5px;
  }
  .nav { position: absolute; top: 57px; right: 99px; display: flex; align-items: center; }
  .nav a {
    color: var(--white); text-decoration: none; font-size: 17.5px; font-weight: 400;
    margin-left: 50px;
  }
  .nav a:first-child { margin-left: 0; }
  .nav .login {
    background: var(--pink); color: var(--white); font-size: 13.5px;
    width: 57px; height: 25px; line-height: 25px; text-align: center;
    border-radius: 3px; margin-left: 49px;
  }
  .thanks {
    position: absolute; left: 0; width: 1200px; top: 250px;
    text-align: center; color: var(--pink); font-size: 48px; font-weight: 600;
    letter-spacing: 0.4px;
  }
  .cta {
    position: absolute; left: 455px; top: 344px; width: 281px; height: 40px;
    border-radius: 20px; background: var(--pink);
    color: var(--white); font-size: 16px; font-weight: 700; text-align: center;
    line-height: 40px; text-decoration: none;
  }
  .back {
    position: absolute; left: 507px; top: 401px;
    display: flex; align-items: center; gap: 12px;
    color: var(--pink); font-size: 17px; text-decoration: none;
  }
  .footer {
    position: absolute; left: 0; top: 578px; width: 1200px; height: 98px;
    background: var(--ink); color: var(--white);
    text-align: center; font-size: 17px; line-height: 86px;
  }
  .footer strong { font-weight: 600; }
</style>
</head>
<body>
<div class="page">
  <header class="hero">
    <div class="hero-photo" role="img" aria-label="Dimmed black and white photograph of a bedroom interior"></div>

    <div class="contact">
      <svg width="17" height="13" viewBox="0 0 17 13" aria-hidden="true">
        <rect x="0.5" y="0.5" width="16" height="12" fill="none" stroke="#fff" stroke-width="1"/>
        <path d="M0.5 0.5 L8.5 7 L16.5 0.5 M0.5 12.5 L6.5 5.5 M16.5 12.5 L10.5 5.5" fill="none" stroke="#fff" stroke-width="1"/>
      </svg>
      <span>hello@velvetkestrel.com</span>
    </div>

    <div class="brand">VelvetKestrel</div>

    <nav class="nav">
      <a href="#">Home</a>
      <a href="#">Membership</a>
      <a href="#">Videos</a>
      <a href="#">Gallery</a>
      <a href="#" class="login">Login</a>
    </nav>

    <h1 class="thanks">THANK YOU FOR JOINING US</h1>
    <a href="#" class="cta">GET INSTANT ACCESS NOW!</a>
    <a href="#" class="back">
      <svg width="30" height="10" viewBox="0 0 30 10" aria-hidden="true">
        <path d="M30 9 H1 L11 1" fill="none" stroke="#eba5cd" stroke-width="1"/>
      </svg>
      <span>Go to Homepage</span>
    </a>
  </header>

  <footer class="footer">
    Copyright © 2020-2021 VelvetKestrel | <strong>Privacy</strong> | <strong>Terms</strong>
  </footer>
</div>
</body>
</html>
```